Bar and Grill needs specials signage

I have attached a file called "daily specials" I need it changed - so there is 1 sign/poster for each day/special
also attached other items to show some styling. I want the new posters chalkboard format, styled along the lines of the drink designs attached.
The designs should be scaleable, and editable, I will print locally

```html
<!DOCTYPE html>
<html lang="en">
<head>
<meta charset="utf-8">
<title>Daily Specials – Monday</title>
<link rel="stylesheet" href="https://fonts.googleapis.com/css2?family=Kaushan+Script&family=Permanent+Marker&family=Special+Elite&display=swap">
<style>
  :root {
    --page: #ffffff;
    --board: #131211;
    --chalk: #f4ead9;
    --chalk-soft: rgba(244, 234, 217, 0.75);
    --accent: #ee7a31;
    --art-tone: #3a3530;
  }
  * { box-sizing: border-box; margin: 0; padding: 0; }
  html, body { width: 1200px; height: 1200px; overflow: hidden; background: var(--page); }
  .canvas { position: relative; width: 1200px; height: 1200px; }

  .board {
    position: absolute; left: 174px; top: 34px; width: 834px; height: 1148px;
    background: var(--board);
  }
  .frame { position: absolute; border: 2px solid var(--chalk-soft); }
  .frame--outer { left: 36px; top: 24px; right: 18px; bottom: 22px; }
  .frame--inner { left: 52px; top: 40px; right: 38px; bottom: 42px; border-width: 1.5px; }

  .header-art { position: absolute; left: 0; top: 0; width: 834px; height: 400px; }
  .heading-arc {
    font-family: "Permanent Marker", cursive;
    font-size: 44px; letter-spacing: 4px; fill: var(--chalk);
  }
  .plate-emblem { fill: var(--accent); }
  .dash { stroke: var(--chalk); stroke-width: 3; stroke-linecap: round; }

  .day-title {
    position: absolute; left: 0; width: 834px; top: 368px;
    text-align: center;
    font-family: "Kaushan Script", cursive;
    font-size: 150px; line-height: 1; color: var(--chalk);
    transform: rotate(-3deg);
  }

  .rule { position: absolute; background: var(--chalk-soft); }
  .rule--top { left: 98px; top: 600px; width: 644px; height: 2px; }
  .rule--bottom { left: 98px; top: 1016px; width: 644px; height: 2px; }
  .rule--left { left: 82px; top: 622px; width: 2px; height: 352px; }
  .rule--mid { left: 392px; top: 622px; width: 2px; height: 352px; }
  .rule--right { left: 756px; top: 622px; width: 2px; height: 352px; }

  .dessert-art {
    position: absolute; left: 100px; top: 630px; width: 276px; height: 350px;
    background: radial-gradient(circle at 50% 45%, var(--art-tone), var(--board) 80%);
  }

  .offer {
    position: absolute; left: 432px; top: 615px; width: 316px;
    font-family: "Kaushan Script", cursive;
    font-size: 54px; line-height: 78px; color: var(--chalk);
    white-space: nowrap;
  }
  .offer__free { color: var(--accent); }

  .site-url {
    position: absolute; left: 0; width: 834px; top: 1046px;
    text-align: center;
    font-family: "Special Elite", monospace;
    font-size: 21px; color: var(--chalk);
  }
</style>
</head>
<body>
<main class="canvas">
  <section class="board">
    <div class="frame frame--outer"></div>
    <div class="frame frame--inner"></div>

    <svg class="header-art" viewBox="0 0 834 400">
      <defs>
        <path id="heading-curve" d="M 218 236 A 222 222 0 0 1 620 236"/>
      </defs>
      <text class="heading-arc">
        <textPath href="#heading-curve" startOffset="50%" text-anchor="middle">DAILY SPECIALS</textPath>
      </text>
      <line class="dash" x1="182" y1="288" x2="252" y2="288"/>
      <line class="dash" x1="190" y1="298" x2="254" y2="298"/>
      <line class="dash" x1="586" y1="288" x2="642" y2="288"/>
      <line class="dash" x1="584" y1="298" x2="650" y2="298"/>
      <circle class="plate-emblem" cx="412" cy="262" r="104" role="img" aria-label="Orange dinner plate flanked by a fork, knife and spoon"/>
    </svg>

    <h1 class="day-title">Monday</h1>

    <div class="rule rule--top"></div>
    <div class="rule rule--left"></div>
    <div class="rule rule--mid"></div>
    <div class="rule rule--right"></div>
    <div class="rule rule--bottom"></div>

    <div class="dessert-art" role="img" aria-label="Chalk drawings of desserts: soft-serve cone, doughnut, slice of pie, wrapped sweets and a muffin"></div>

    <p class="offer">Kids Eat <span class="offer__free">free</span><br>From Our<br>Kids Menu,<br>With Adult<br>Purchase</p>

    <p class="site-url">www.hollowoakgrill.com</p>
  </section>
</main>
</body>
</html>
```